Business Card for Inovative Flexible Packaging Company

Create a business card that is both simple and stricking at the same time.
Preferably only one color (orange) or two colors (black and orange).
Information to print:
Lumtrex, Lda
[T] 22 418 6095
[M] 91 362 7148
[F] 22 418 6037
[@] lumtrex.ac@mailvora.com
SEDE & ARMAZÉM
Rua Das Figueiras do Monte, 317
Valmoura
4415-238 Valmoura - VN Alcora
LUSITERA
Reason: A lot of the ideas are obvious. I want something different. Inovative. dare to do something eye catching with style.
Target Market(s)
Business Consumers. Packaging Designers.
Industry/Entity Type
Business
Look and feel
Each slider illustrates characteristics of the customer's brand and the style your logo design should communicate.

```html
<!DOCTYPE html>
<html lang="pt">
<head>
<meta charset="utf-8">
<title>Lumtrex — Business Card</title>
<link rel="stylesheet" href="https://fonts.googleapis.com/css2?family=Montserrat:wght@300;400;500;600&display=swap">
<style>
  :root {
    --backdrop: #e6e4e1;
    --card: #f4f4f3;
    --orange: #e8731a;
    --ink: #2e2e2e;
    --shadow: rgba(0, 0, 0, 0.14);
  }
  * { box-sizing: border-box; margin: 0; padding: 0; }
  html, body {
    width: 1200px;
    height: 900px;
    overflow: hidden;
    background: var(--backdrop);
    font-family: "Montserrat", Arial, sans-serif;
    color: var(--ink);
  }
  .stage {
    position: relative;
    width: 1200px;
    height: 900px;
    display: flex;
    align-items: center;
    justify-content: center;
    gap: 90px;
  }
  .card {
    background: var(--card);
    box-shadow: 0 12px 30px var(--shadow);
  }

  /* Back: contact side, portrait */
  .card-back {
    width: 390px;
    height: 680px;
    padding: 54px 40px 52px;
    display: flex;
    flex-direction: column;
    align-items: center;
  }
  .brand {
    display: flex;
    align-items: center;
    gap: 12px;
  }
  .brand-mark {
    width: 18px;
    height: 18px;
    background: var(--orange);
  }
  .brand-name {
    font-size: 44px;
    font-weight: 600;
    color: var(--orange);
    letter-spacing: -0.5px;
    line-height: 1;
  }
  .contact-list {
    list-style: none;
    width: 100%;
    flex: 1;
    margin-top: 38px;
    display: flex;
    flex-direction: column;
    justify-content: space-between;
    text-align: center;
  }
  .contact-label {
    display: flex;
    align-items: center;
    gap: 14px;
    font-size: 15px;
    font-weight: 400;
    letter-spacing: 1.5px;
    color: var(--orange);
    text-transform: uppercase;
    margin-bottom: 8px;
  }
  .contact-label::before,
  .contact-label::after {
    content: "";
    flex: 1;
    height: 1px;
    background: var(--orange);
  }
  .contact-value {
    font-size: 17px;
    font-weight: 400;
    line-height: 1.4;
  }
  .address {
    font-style: normal;
    font-size: 16px;
  }

  /* Front: landscape, name only */
  .card-front {
    width: 620px;
    height: 360px;
    display: flex;
    align-items: center;
    justify-content: center;
    gap: 16px;
  }
  .card-front .brand-mark { width: 30px; height: 30px; }
  .card-front .brand-name { font-size: 64px; }
</style>
</head>
<body>
<main class="stage">
  <section class="card card-back" aria-label="Card back with contact details">
    <div class="brand">
      <span class="brand-mark"></span>
      <span class="brand-name">lumtrex</span>
    </div>
    <ul class="contact-list">
      <li class="contact-item">
        <div class="contact-label">Phone</div>
        <div class="contact-value">22 418 6095</div>
      </li>
      <li class="contact-item">
        <div class="contact-label">Mobile</div>
        <div class="contact-value">91 362 7148</div>
      </li>
      <li class="contact-item">
        <div class="contact-label">Fax</div>
        <div class="contact-value">22 418 6037</div>
      </li>
      <li class="contact-item">
        <div class="contact-label">Email</div>
        <div class="contact-value">lumtrex.ac@mailvora.com</div>
      </li>
      <li class="contact-item">
        <div class="contact-label">Address</div>
        <address class="contact-value address">
          SEDE &amp; ARMAZÉM<br>
          Rua Das Figueiras do Monte, 317<br>
          Valmoura<br>
          4415-238 Valmoura - VN Alcora<br>
          Lusitera
        </address>
      </li>
    </ul>
  </section>

  <section class="card card-front" aria-label="Card front">
    <span class="brand-mark"></span>
    <span class="brand-name">lumtrex</span>
  </section>
</main>
</body>
</html>
```